Corvel Capital LLC

Need Professional Business cards for New Investment Fund

Target Market(s)

High Quality investors

Industry/Entity Type

Financial

Contact Information for Business Card

Phone Number +1 555 284 6190
Name Lukas Varenko
Title Fund Manager
email lv@FundCorvel.com
Website www.FundCorvel.com

Colors

Designer to choose colors to be used in the design.

Requirements
Must have
• Must have our Logo and all of the above. Must be made so lettering and loge can be raised

```html
<!DOCTYPE html>
<html lang="en">
<head>
<meta charset="utf-8">
<title>Corvel Capital LLC – Business Card</title>
<link rel="stylesheet" href="https://fonts.googleapis.com/css2?family=Oswald:wght@500&family=Montserrat:wght@300;500&display=swap">
<style>
  :root {
    --backdrop: #6f6f6f;
    --card: #262626;
    --edge: #1fd61a;
    --accent: #3ff020;
    --text-light: #e6e6e6;
    --mark-text: #3ff020;
  }
  * { box-sizing: border-box; margin: 0; padding: 0; }
  html, body { width: 1200px; height: 1074px; overflow: hidden; }
  body {
    background: var(--backdrop);
    font-family: "Montserrat", sans-serif;
    position: relative;
  }
  .card {
    position: absolute;
    left: 240px;
    width: 720px;
    height: 412px;
    background: var(--card);
    border-bottom: 4px solid var(--edge);
    border-right: 2px solid var(--edge);
  }
  .card--front { top: 90px; }
  .card--back { top: 572px; }

  .brand {
    position: absolute;
    display: flex;
    align-items: center;
    gap: 14px;
    font-family: "Montserrat", sans-serif;
    font-weight: 500;
    color: var(--mark-text);
    letter-spacing: 0.04em;
    text-transform: uppercase;
  }
  .brand__square {
    width: 22px; height: 22px;
    background: var(--accent);
  }
  .card--front .brand { left: 60px; top: 186px; font-size: 24px; }
  .card--back .brand { left: 50%; top: 50%; transform: translate(-50%, -50%); font-size: 34px; }
  .card--back .brand__square { width: 30px; height: 30px; }

  .person {
    position: absolute;
    left: 420px;
    top: 92px;
  }
  .person__name {
    font-family: "Oswald", sans-serif;
    font-weight: 500;
    font-size: 34px;
    color: var(--accent);
    text-transform: uppercase;
    letter-spacing: 0.01em;
    line-height: 1.1;
  }
  .person__title {
    font-weight: 300;
    font-size: 19px;
    color: var(--text-light);
    margin-top: 4px;
  }
  .icons {
    display: flex;
    gap: 6px;
    margin: 22px 0 20px;
  }
  .icons svg { width: 20px; height: 20px; }
  .contact {
    list-style: none;
    font-weight: 300;
    font-size: 17px;
    color: var(--text-light);
    line-height: 1.45;
  }
</style>
</head>
<body>
  <section class="card card--front" aria-label="Business card front">
    <div class="brand"><span class="brand__square"></span>Corvel Capital</div>
    <div class="person">
      <h1 class="person__name">Lukas Varenko</h1>
      <p class="person__title">Fund Manager</p>
      <div class="icons">
        <svg viewBox="0 0 20 20" aria-label="Phone"><circle cx="10" cy="10" r="10" fill="var(--accent)"/><path d="M7 5.5l1.6 2-1 1.2a6 6 0 0 0 3.7 3.7l1.2-1 2 1.6-1 1.5c-3.8.2-7.9-3.9-7.7-7.7z" fill="var(--card)"/></svg>
        <svg viewBox="0 0 20 20" aria-label="Email"><circle cx="10" cy="10" r="10" fill="var(--accent)"/><rect x="5" y="6.5" width="10" height="7" fill="var(--card)"/><path d="M5 6.5l5 4 5-4" stroke="var(--accent)" stroke-width="1" fill="none"/></svg>
        <svg viewBox="0 0 20 20" aria-label="Website"><circle cx="10" cy="10" r="10" fill="var(--accent)"/><circle cx="10" cy="10" r="5" fill="none" stroke="var(--card)" stroke-width="1.4"/><path d="M5 10h10M10 5c-2.5 3-2.5 7 0 10M10 5c2.5 3 2.5 7 0 10" stroke="var(--card)" stroke-width="1.2" fill="none"/></svg>
      </div>
      <ul class="contact">
        <li>+1 555 284 6190</li>
        <li>lv@FundCorvel.com</li>
        <li>FundCorvel.com</li>
      </ul>
    </div>
  </section>

  <section class="card card--back" aria-label="Business card back">
    <div class="brand"><span class="brand__square"></span>Corvel Capital</div>
  </section>
</body>
</html>
```